Stylish Business Cards Wanted

- DOUBLE SIDED Design Required -

High end, edgy cards for a corporate and personal stylist. Must include logo,
Name: Belinda Harwick
Title: Director and Stylist
telephone : +61 8 7142 5809
email: belinda@theloombriefing.example
website: theloombriefing.example
Tag: Corporate Workwear & Uniform Specialist | Personal Stylist
Would like nice icons for telephone, email, website

Target Market(s)

Businesses wanting stylish uniforms, people wanting stylish wardrobes

Industry/Entity Type

Corporate Workwear Stylist

Contact Information for Business Card

I would like black, white and gold foiling incorporated in the design - possibly a touch of the other colours on my branding guide attached Name: Belinda Harwick Title: Director and Stylist telephone : +61 8 7142 5809 email: belinda@theloombriefing.example website: theloombriefing.example Tag: Corporate Workwear & Uniform Specialist | Personal Stylist Would like nice icons for telephone, email, website

Font styles to use
Other font styles liked:
• Raleway

Colors

Designer to choose colors to be used in the design.

Requirements
Must have
• Gold foil accents

```html
<!DOCTYPE html>
<html lang="en">
<head>
<meta charset="utf-8">
<title>The Loom Briefing — Business Cards</title>
<link href="https://fonts.googleapis.com/css2?family=Raleway:wght@400;500;700;800&display=swap" rel="stylesheet">
<style>
  :root {
    --backdrop: #2c2f34;
    --card: #1f1f20;
    --gold: #e5b23a;
    --white: #f4f4f2;
    --silver: #8d8e91;
    --muted: #cfcfcf;
  }
  * { box-sizing: border-box; margin: 0; padding: 0; }
  html, body {
    width: 1200px; height: 900px; overflow: hidden;
    background: var(--backdrop);
    font-family: "Raleway", sans-serif;
  }
  .sheet {
    width: 1200px; height: 900px;
    display: flex; flex-direction: column;
    align-items: center; justify-content: center; gap: 56px;
  }
  .card {
    position: relative;
    width: 620px; height: 354px;
    background: var(--card);
    border-radius: 24px;
    box-shadow: 0 14px 30px rgba(0,0,0,.45);
    overflow: hidden;
  }

  /* Front: contact side */
  .identity {
    position: absolute; left: 48px; top: 46px;
    padding-left: 18px;
    border-left: 7px solid var(--gold);
  }
  .identity__name {
    color: var(--gold); font-weight: 800;
    font-size: 25px; letter-spacing: .5px; text-transform: uppercase;
    line-height: 1.05;
  }
  .identity__title {
    color: var(--muted); font-size: 15px; font-weight: 500; margin-top: 4px;
  }
  .contacts {
    position: absolute; left: 48px; top: 148px;
    list-style: none;
  }
  .contacts__item {
    display: flex; align-items: center; gap: 12px;
    color: var(--white); font-size: 16px; font-weight: 500;
    line-height: 1; margin-bottom: 14px;
  }
  .contacts__icon { width: 16px; height: 16px; flex: none; }
  .front .wordmark {
    position: absolute; right: 44px; bottom: 44px;
    display: flex; align-items: center; gap: 12px;
  }
  .wordmark__text {
    color: var(--white); font-weight: 700; font-size: 34px; line-height: 1;
  }
  .wordmark__square {
    width: 14px; height: 14px; background: var(--gold);
  }

  /* Back: brand side */
  .back .wordmark {
    position: absolute; left: 0; right: 0; top: 118px;
    display: flex; justify-content: center; align-items: center; gap: 14px;
  }
  .back .wordmark__text { color: var(--silver); font-size: 46px; }
  .tagline {
    position: absolute; left: 0; right: 0; bottom: 52px;
    text-align: center;
    color: var(--gold); font-size: 15px; font-weight: 500;
    letter-spacing: 1px; text-transform: uppercase;
  }
</style>
</head>
<body>
<main class="sheet">

  <section class="card front" aria-label="Card front">
    <div class="identity">
      <h1 class="identity__name">Belinda Harwick</h1>
      <p class="identity__title">Director and Stylist</p>
    </div>
    <ul class="contacts">
      <li class="contacts__item">
        <svg class="contacts__icon" viewBox="0 0 16 16" aria-hidden="true">
          <path fill="#e5b23a" d="M3.3 1.2l2.2 2.6c.3.4.3.9-.1 1.3L4.3 6.2c.9 2 2.5 3.6 4.5 4.5l1.1-1.1c.4-.4.9-.4 1.3-.1l2.6 2.2c.4.3.4.9.1 1.3l-1.3 1.5c-.4.4-1 .6-1.6.4C5.8 13.6 2.4 10.2.9 5.1.7 4.5.9 3.9 1.3 3.5L2 2.2c.4-.4 1-.4 1.3-1z"/>
        </svg>
        +61 8 7142 5809
      </li>
      <li class="contacts__item">
        <svg class="contacts__icon" viewBox="0 0 16 16" aria-hidden="true">
          <rect x="1" y="3" width="14" height="10" rx="1.5" fill="#e5b23a"/>
          <path d="M1.8 4l6.2 5 6.2-5" fill="none" stroke="#1f1f20" stroke-width="1.4"/>
        </svg>
        belinda@theloombriefing.example
      </li>
      <li class="contacts__item">
        <svg class="contacts__icon" viewBox="0 0 16 16" aria-hidden="true">
          <circle cx="8" cy="8" r="6.8" fill="none" stroke="#e5b23a" stroke-width="1.5"/>
          <ellipse cx="8" cy="8" rx="3" ry="6.8" fill="none" stroke="#e5b23a" stroke-width="1.3"/>
          <path d="M1.5 8h13" stroke="#e5b23a" stroke-width="1.3"/>
        </svg>
        www.theloombriefing.example
      </li>
    </ul>
    <div class="wordmark">
      <span class="wordmark__square"></span>
      <span class="wordmark__text">The Loom Briefing</span>
    </div>
  </section>

  <section class="card back" aria-label="Card back">
    <div class="wordmark">
      <span class="wordmark__square"></span>
      <span class="wordmark__text">The Loom Briefing</span>
    </div>
    <p class="tagline">Corporate Workwear | Uniform Specialist | Personal Stylist</p>
  </section>

</main>
</body>
</html>
```